Website offering services oriented to the metaverse and blockchain

We need an ecommerce website theme/template for a new company named Vimbral (a play on words for KORVAND the inventor of Quorvex). Vimbral will provide metaverse services such as:
• Vimbral Coin
• Vimbral wallet
• Vimbral Exchange
• Vimbral NFT
• Vimbral Tech
• Vimbral Pay
• Vimbral CaaS (community as a service)
• Vimbral CRM
• Vimbral Experience
• Vimbral Blockchain
• Vimbral Commerce
• Vimbral Space (as in outer space)
• Vimbral Art (sub of NFT)
• Vimbral Store

You can find our actual logo at the following link, in order to show us templates aligned with our brand:
https://files.brindlevault.net/share/folders/8kLmTzqWpXcVbNdRyHsEfGaUoJi2QtYxP?mode=view

Looking forward to heard back from you,

Designs look the same

We need a WordPress ecommerce website theme/template for a new company named Vimbral (a play on words for KORVAND the inventor of Quorvex). Vimbral will provide metaverse services such as: • Vimbral Coin • Vimbral wallet • Vimbral Exchange • Vimbral NFT • Vimbral Tech • Vimbral Pay • Vimbral CaaS (community as a service) • Vimbral CRM • Vimbral Experience • Vimbral Blockchain • Vimbral Commerce • Vimbral Space (as in outer space) • Vimbral Art (sub of NFT) • Vimbral Store You can find our actual logo at the following link, in order to show us templates aligned with our brand: https://files.brindlevault.net/share/folders/8kLmTzqWpXcVbNdRyHsEfGaUoJi2QtYxP?mode=view Looking forward to heard back from you,

Target Market(s)

Blockchain & Cryptocurrency Businesses

Industry/Entity Type

B2C, B2B Services.

Other font styles liked:
• Monserrat, Helvetica, Object Sans

Requirements
Nice to have
• Light background picture,
Should not have
• Arch designs

```html
<!DOCTYPE html>
<html lang="en">
<head>
<meta charset="utf-8">
<title>Vimbral — Metaverse & Blockchain Services</title>
<link rel="stylesheet" href="https://fonts.googleapis.com/css2?family=Montserrat:wght@800;900&family=Roboto:wght@400;500;700;900&display=swap">
<style>
:root{
  --navy:#020c18;
  --navy-2:#04182e;
  --glow:#0a5fb0;
  --orange:#f0960e;
  --white:#ffffff;
  --ink:#141414;
  --grey:#8c8c8c;
  --sky:#d6ebf5;
  --plum:#36093a;
  --forest:#1c6a4b;
  --line:#ececec;
}
*{margin:0;padding:0;box-sizing:border-box}
html,body{width:1200px;height:3937px;overflow:hidden}
body{position:relative;background:var(--white);font-family:"Roboto",Helvetica,Arial,sans-serif;color:var(--ink)}
.abs{position:absolute}
.btn{position:absolute;display:flex;align-items:center;justify-content:center;background:var(--orange);color:var(--white);font-weight:700;border-radius:40px;text-transform:uppercase;text-decoration:none}
.heading{font-family:"Montserrat",Helvetica,sans-serif;font-weight:900;letter-spacing:-1px;text-transform:uppercase}

/* hero */
.hero{position:absolute;left:0;top:0;width:1200px;height:1087px;background:var(--navy)}
.hero-art{position:absolute;left:0;top:0;width:1200px;height:740px;
  background:radial-gradient(ellipse 560px 180px at 600px 620px,#1a7fe0 0%,#0b3f7c 35%,rgba(2,12,24,0) 75%),
  radial-gradient(ellipse 700px 420px at 600px 300px,#06284d 0%,rgba(2,12,24,0) 70%),
  linear-gradient(#01060d,#031426 60%,var(--navy))}
.logo{left:144px;top:48px;font-family:"Roboto",sans-serif;font-weight:900;font-size:46px;color:var(--white);letter-spacing:-1px}
.nav{left:493px;top:60px;display:flex;gap:35px;font-size:14px;font-weight:500;color:var(--white)}
.nav span.active{border-bottom:2px solid var(--orange);padding-bottom:8px}
.login{left:938px;top:44px;width:117px;height:53px;font-size:16px}
.hero-title{left:0;width:1200px;top:195px;text-align:center;font-weight:900;font-size:108px;color:var(--white);letter-spacing:-2px}
.hero-sub{left:0;width:1200px;top:342px;text-align:center;font-size:21px;font-weight:500;line-height:31px;color:var(--white)}
.start{left:509px;top:436px;width:180px;height:50px;font-size:16px}
.scroll{left:588px;top:612px}
.about-title{left:155px;top:800px;font-size:58px;color:var(--white)}
.about-text{left:481px;top:803px;width:565px;font-size:13.5px;line-height:25.6px;color:#dfe6ee}
.about-btn{left:481px;top:955px;width:158px;height:52px;font-size:16px}

/* tiles */
.tile{position:absolute;top:1087px;width:600px;height:376px}
.tile.crypto{left:0;background:linear-gradient(120deg,#2c8c6c,#6fe3bb 45%,#1f5f4c)}
.tile.chain{left:600px;background:linear-gradient(135deg,#3a0b44,#7e1f8a 55%,#b150c2)}
.tile-label{position:absolute;height:63px;top:1353px;display:flex;align-items:center;justify-content:center;color:var(--white);font-weight:700;font-size:34px;text-transform:uppercase}
.tile-label.crypto{left:90px;width:419px;background:var(--plum)}
.tile-label.chain{left:691px;width:417px;background:var(--forest)}

/* services */
.wwd{left:0;width:1200px;top:1560px;text-align:center;font-size:56px}
.service{position:absolute;width:300px;text-align:center}
.service.featured{left:451px;top:1686px;height:393px;background:var(--white);border-radius:22px;box-shadow:0 6px 28px rgba(0,0,0,.12)}
.service h3{font-size:17px;font-weight:700;text-transform:uppercase;color:#1a1a1a}
.service p{margin-top:14px;font-size:13px;line-height:25px;color:var(--grey);padding:0 18px}
.service .sbtn{position:relative;margin:22px auto 0;width:119px;height:33px;font-size:12.5px;box-shadow:0 3px 8px rgba(240,150,14,.35)}
.service .icon{display:block;margin:0 auto 22px}

/* why us */
.why-shape{left:0;top:2160px}
.why-title{left:144px;top:2340px;font-size:58px}
.why-text{left:144px;top:2434px;width:380px;font-size:13.5px;line-height:24.8px;color:var(--grey)}
.why-btn{left:144px;top:2643px;width:158px;height:52px;font-size:16px}
.laptop-screen{left:586px;top:2368px;width:468px;height:304px;border:4px solid #2a2a2a;border-radius:14px 14px 0 0;background:linear-gradient(160deg,#0b0b0b,#113a1c 55%,#0b0b0b)}
.laptop-base{left:540px;top:2672px;width:558px;height:14px;background:linear-gradient(#e4e4e4,#9a9a9a);border-radius:0 0 40px 40px}

/* blog */
.blog-title{left:0;width:1200px;top:3022px;text-align:center;font-size:56px}
.card{position:absolute;background:var(--white);border:1px solid var(--line);border-radius:22px;box-shadow:0 3px 12px rgba(0,0,0,.04)}
.thumb{position:absolute;border-radius:20px}
.post-date{font-size:12.5px;color:var(--orange)}
.post-title{margin-top:18px;font-size:18.5px;font-weight:500;line-height:25px;color:#1a1a1a}
.post-text{margin-top:16px;font-size:12px;line-height:25.6px;color:var(--grey)}
.post-more{margin-top:14px;font-size:15px;font-weight:700;color:var(--forest);text-transform:uppercase}
.post-body{position:absolute}

/* footer */
.footer{left:0;top:3776px;width:1200px;height:161px;background:var(--navy)}
.social{position:absolute;top:3753px;width:42px;height:42px;border-radius:50%;background:var(--white);border:2px solid var(--navy)}
.social::after{content:"";position:absolute;left:14px;top:14px;width:10px;height:10px;border-radius:50%;background:var(--navy)}
.foot-nav{left:0;width:1200px;top:3834px;display:flex;justify-content:center;gap:28px;color:var(--white);font-size:19px;font-weight:700;text-transform:uppercase}
.copy{left:0;width:1200px;top:3884px;text-align:center;color:var(--white);font-size:12px}
</style>
</head>
<body>

<section class="hero">
  <div class="hero-art" role="img" aria-label="Glowing digital globe with floating crypto coins and circuit light lines"></div>
  <div class="abs logo">VIMBRAL</div>
  <nav class="abs nav"><span class="active">HOME</span><span>ABOUT</span><span>SERVICES</span><span>NEWS</span><span>CONTACT</span></nav>
  <a class="btn login">Login</a>
  <h1 class="abs hero-title">VIMBRAL</h1>
  <p class="abs hero-sub">Sed ut perspiciatis unde omnis iste natus errvoluptatem<br>accusantium doloremque laudantium</p>
  <a class="btn start">Get Started</a>
  <svg class="abs scroll" width="24" height="40" viewBox="0 0 24 40" fill="none" stroke="#fff" stroke-width="3" stroke-linejoin="round">
    <path d="M3 12 L12 3 L21 12"/><path d="M3 21 L12 12 L21 21"/><path d="M3 28 L12 37 L21 28"/><path d="M3 19 L12 28 L21 19"/>
  </svg>
  <h2 class="abs heading about-title">About</h2>
  <p class="abs about-text">Lorem ipsum dolor sit amet, consectetur adipiscing elit, sed do eiusmod tempor incididunt ut labore et dolore magna aliqua ipsum suspendisse ultrices gravida. Risus commodo viverra maecenas accumsan lacus vel facilisis ipsum dolor sit amet, consectetur adipiscing elit, sed do eiusmod tempor incididunt ut labore et dolore magna aliqua ipsum suspendisse ultrices gravida. Risus commodo viverra maecenas accumsan lacus vel facilisis.</p>
  <a class="btn about-btn">Read More</a>
</section>

<div class="tile crypto" role="img" aria-label="Laptop and phone showing trading charts, tinted mint green"></div>
<div class="tile chain" role="img" aria-label="Abstract digital city of data blocks, tinted purple"></div>
<div class="tile-label crypto">Cryptocurrency</div>
<div class="tile-label chain">Blockchain</div>

<h2 class="abs heading wwd">What We Do</h2>

<div class="service" style="left:117px;top:1722px">
  <svg class="icon" width="76" height="76" viewBox="0 0 76 76" fill="none" stroke="#1c6a4b" stroke-width="3">
    <circle cx="38" cy="40" r="26"/><circle cx="38" cy="46" r="11"/><path d="M14 40 h10 l4 -8 l5 14 l5 -10 h24"/><path d="M38 6 v14"/>
  </svg>
  <h3>Inventore</h3>
  <p>Sed ut perspiciatis unde omnis iste natus error sit voluptatem accutiumoloremque laudantium, totam rem aperiame aque ipsa quae</p>
  <a class="btn sbtn">Read More</a>
</div>

<div class="service featured">
  <svg class="icon" width="78" height="78" viewBox="0 0 78 78" fill="none" stroke="#36093a" stroke-width="3" style="margin-top:34px">
    <circle cx="30" cy="46" r="22"/><circle cx="52" cy="28" r="18"/><path d="M52 18 v20 M46 24 h10 M46 32 h10"/><path d="M24 38 h10 a5 5 0 0 1 0 8 h-10 v-8 M24 46 h11 a5 5 0 0 1 0 9 h-11 z"/>
  </svg>
  <h3>Nemo Enim Ipsam</h3>
  <p>Sed ut perspiciatis unde omnis iste natus error sit voluptatem accutiumoloremque laudantium, totam rem aperiame aque ipsa quae</p>
  <a class="btn sbtn">Read More</a>
</div>

<div class="service" style="left:781px;top:1722px">
  <svg class="icon" width="76" height="76" viewBox="0 0 76 76" fill="none" stroke="#1c6a4b" stroke-width="3" stroke-linejoin="round">
    <path d="M38 6 l10 6 v12 l-10 6 l-10 -6 v-12 z"/><path d="M18 28 l10 6 v12 l-10 6 l-10 -6 v-12 z"/><path d="M58 28 l10 6 v12 l-10 6 l-10 -6 v-12 z"/><path d="M38 46 l10 6 v12 l-10 6 l-10 -6 v-12 z"/>
  </svg>
  <h3>Neque Porro Quis</h3>
  <p>Sed ut perspiciatis unde omnis iste natus error sit voluptatem accutiumoloremque laudantium, totam rem aperiame aque ipsa quae</p>
  <a class="btn sbtn">Read More</a>
</div>

<svg class="abs why-shape" width="1200" height="770" viewBox="0 0 1200 770">
  <path fill="#d6ebf5" d="M210 0 L1040 95 C1110 105 1140 160 1140 250 L1140 500 C1140 600 1080 650 990 665 L215 763 C120 775 58 700 58 600 L58 160 C58 60 120 -10 210 0 Z"/>
</svg>
<h2 class="abs heading why-title">Why Us?</h2>
<p class="abs why-text">Lorem ipsum dolor sit amet, consectetur adipiscing elit, sed do eiusmod tempor incididunt ut labore et dolore magna aliqua. Quis ipsum suspendisse ultrices gravidsus commodo viverra maecenas accumsan lacus vel facilisisem ipsum dolor sit amet, consectetur adipiscing elit, sed do eiusmod tempor incididunt ut labore et dolore magna aliqupsum suspendisse ultrices gravids commoaecenaan lacus vel facilisis.</p>
<a class="btn why-btn">Read More</a>
<div class="abs laptop-screen" role="img" aria-label="Laptop showing a crypto trading dashboard with price chart and buy and sell controls"></div>
<div class="abs laptop-base"></div>

<h2 class="abs heading blog-title">Blog Posts</h2>

<article class="card" style="left:141px;top:3154px;width:298px;height:509px">
  <div class="thumb" style="left:2px;top:0;width:292px;height:224px;background:radial-gradient(circle at 50% 45%,#1ec8ff 0%,#0b4fa8 30%,#061a3a 75%)" role="img" aria-label="Glowing coin on a blue circuit board"></div>
  <div class="post-body" style="left:22px;top:252px;width:256px">
    <div class="post-date">Aug,2019</div>
    <div class="post-title">Sed ut perspiciatis unde omnis iste natus</div>
    <div class="post-text">Ut enim ad minima veniam, quis nostreierci tationem ullam corporis suscipit labori-osan isi ut aliquid ex ea commodi eprehen-deritq ui in ea voluptate velit .</div>
    <div class="post-more">Read More</div>
  </div>
</article>

<article class="card" style="left:456px;top:3154px;width:602px;height:247px">
  <div class="thumb" style="left:0;top:0;width:236px;height:245px;background:linear-gradient(170deg,#0a1730,#1a2f5a 55%,#3a3f6a)" role="img" aria-label="Night city skyline with glowing network connections"></div>
  <div class="post-body" style="left:268px;top:33px;width:310px">
    <div class="post-date">Aug,2019</div>
    <div class="post-title" style="margin-top:12px">Sed ut perspiciatis unde omnis iste natus error</div>
    <div class="post-text" style="margin-top:10px">Ut enim ad minima veniam, quis nostreierci tationem ullam corporis suscipit laboriosan isi ut aliquid ex ea eprehenderitq utate velit .</div>
    <div class="post-more" style="margin-top:10px">Read More</div>
  </div>
</article>

<article class="card" style="left:456px;top:3416px;width:602px;height:247px">
  <div class="thumb" style="left:0;top:0;width:236px;height:245px;background:linear-gradient(150deg,#071f30,#0d3b52 55%,#0a2a3e)" role="img" aria-label="Connected glowing cubes forming a blockchain network"></div>
  <div class="post-body" style="left:268px;top:33px;width:310px">
    <div class="post-date">Aug,2019</div>
    <div class="post-title" style="margin-top:12px">Sed ut perspiciatis unde omnis iste natus error</div>
    <div class="post-text" style="margin-top:10px">Ut enim ad minima veniam, quis nostreierci tationem ullam corporis suscipit laboriosan isi ut aliquid ex ea eprehenderitq utate velit .</div>
    <div class="post-more" style="margin-top:10px">Read More</div>
  </div>
</article>

<footer class="abs footer"></footer>
<span class="social" style="left:508px" aria-label="Social link"></span>
<span class="social" style="left:555px" aria-label="Social link"></span>
<span class="social" style="left:601px" aria-label="Social link"></span>
<span class="social" style="left:649px" aria-label="Social link"></span>
<nav class="abs foot-nav"><span>Home</span><span>/</span><span>About</span><span>/</span><span>Services</span><span>/</span><span>News</span><span>/</span><span>Contact</span></nav>
<p class="abs copy">Copyrights © 2021, Vimbral.All rights reserved &nbsp;|&nbsp; Privacy policy &nbsp;|&nbsp; Site Map &nbsp;|&nbsp; Disclaimer &nbsp;|&nbsp; Terms of use</p>

</body>
</html>
```